Interior Design for Every Day, Nora Whitfield Interior Design, LLC

We are looking for a website for an Interior Design Company targeted at higher income households. We prefer to work with clients that seek to amplify the architectural beauty of their interior space via interior design - while ensuring the space promotes easy living. For example: a kitchen should be lain out in an intuitive manner such that all utensils, cups and plates are easy to find. Living rooms should be arranged to promote conversation and/or watch TV, etc.... We have heavy reliance on the technical aspects of design (computer automated renderings). We like the look and feel of this website: https://www.brenthalvorsen.example/portfolioall

Target Market(s)

Upper HHI ($200,000+) in the Atlanta Metro Market. Customers are likely to be highly educated and from a variety of cultural backgrounds. Ages 35-60

Industry/Entity Type

Architecture

Font styles to use
Sans Serif

Colors

Designer to choose colors to be used in the design.

Requirements
Must have
• Landing Page, Page demonstrating how interior design fits into the architectural design process, About Us Page with contact info, Example Work Page and Tailored Client Page. Minimal work can be done on the About Us and example work pages. The tailored client page just needs a good layout (and easy uploads and download capability)
• Also to include:
• (1) The landing page should include a Design Philosophy Section and maybe a couple examples of our work and/or pictures you provide
• (2) The Design Process page should explain all steps of the architectural Design process and should explain where interior design/decorating fits into the Architectural process (see below attachments).
• (3) The Example work page should include areas for portfolio example uploads (to include 3 dimensional and 2 dimensional renderings, photos and videos).
• (4) Include a Password Protected, Secure Place where each individual client can store and retrieve documents and work product for their project (Should be a separate page). There should be sections (for each client) for:
• (a) there should be a client account creation requirement page that requires: FN, LN, Mobile, email, Work phone, Property address, City, Zip (for 3 properties), Spouse FN, Spouse LN, Child FN, LN (space for 5 children)
• (a) section: Legal & Invoices
• (b) section: Drawings & Renderings
• (c) section: Pin Ups (easy uploads of pictures from sites like snapboardia would be appreciated) - pin ups should be very easy for clients to put examples of what they like
• (5) Ability for admin to use personalized password and username to view, delete and edit client files (we utilize filecrate for document storage currently, and integration with filecrate would be a plus)
• (6) needs to be formatted and optimized for Mobile (iOs and android) viewing as well as Web
• (7) The site should be built with a hosting service contemplated. This service should be affordable (Less than $300 per annum)
• (8) most importantly the site should be minimalist with focus on user friendliness while being fashion forward
• (9) Website Color scheme should be White/Black/BlueGrey
• (10) The site must also include the ability to generate an invoice, based on client registration, electronically submit the invoice to the client via email (or print it), accept payment via coinvoy integration, and generate conformation email of payment to both client and admin (although coinvoy may already do this).
Nice to have
• Ability of example and client pages to be integrated with sites like snapbordia and filecrate. Ability to have some sort of section that self identifies the clients design style(s)...maybe a quiz or at lease a place where they can create a pinboard of images and colors they like (potentially by room)
Should not have
• Must look modern and be extremely quick/user friendly. Our clients are very busy.

```html
<!DOCTYPE html>
<html lang="en">
<head>
<meta charset="utf-8">
<title>Nora Whitfield Interior Design – Client Registration</title>
<link rel="stylesheet" href="https://fonts.googleapis.com/css2?family=Roboto:wght@300;400&family=Roboto+Condensed:wght@700&family=Source+Sans+3:wght@400;600&display=swap">
<style>
:root{
  --ink:#333333;
  --muted:#8a8a8a;
  --rule:#e3e3e3;
  --panel:#f4f4f4;
  --field-border:#a8a8a8;
  --blue:#2b73b4;
  --footer:#222222;
  --footer-text:#e6e6e6;
  --chip:#d9d9d9;
}
*{box-sizing:border-box;margin:0;padding:0}
html,body{width:1143px;height:1200px;overflow:hidden;background:#fff}
.page{position:relative;width:1143px;height:1200px;font-family:"Source Sans 3",sans-serif;color:var(--ink)}
.brand{position:absolute;left:0;top:46px;width:1143px;display:flex;justify-content:center;align-items:center;gap:10px;font-family:"Roboto",sans-serif;font-weight:300;font-size:22px;letter-spacing:3px;color:var(--ink);text-transform:uppercase;white-space:nowrap}
.brand .mark{width:12px;height:12px;background:var(--ink)}
.rule-top{position:absolute;left:153px;top:121px;width:837px;height:1px;background:var(--rule)}
.rule-nav{position:absolute;left:218px;top:160px;width:708px;height:1px;background:var(--rule)}
.nav a{position:absolute;top:134px;transform:translateX(-50%);font-family:"Roboto",sans-serif;font-size:11px;letter-spacing:2.6px;color:var(--muted);text-decoration:none;white-space:nowrap}
.hero{position:absolute;left:153px;top:181px;width:836px;height:483px;background:
  linear-gradient(180deg,#6f6672 0%,#847b87 40%,#6e6672 68%,#b5b0b5 85%,#d2cfd2 100%)}
.register{position:absolute;left:0;top:719px;width:1143px;height:423px;background:var(--panel)}
.title{position:absolute;left:0;width:1143px;text-align:center}
.title-top{top:34px;font-family:"Roboto",sans-serif;font-weight:300;font-size:25px;color:var(--ink)}
.title-main{top:57px;font-family:"Roboto Condensed",sans-serif;font-weight:700;font-size:38px;color:var(--blue);letter-spacing:-1px}
.field{position:absolute;width:262px;height:32px;border:1px solid var(--field-border);border-radius:3px;background:#fff;display:flex;align-items:center;padding:0 9px;font-size:13px;color:var(--ink);letter-spacing:-.2px}
.field svg.ico{width:10px;height:10px;margin-right:3px;fill:var(--ink)}
.field .chev{position:absolute;right:18px;top:12px;width:8px;height:6px}
.submit{position:absolute;left:514px;top:361px;width:97px;height:29px;border-radius:15px;background:var(--blue);color:#fff;font-weight:600;font-size:14px;display:flex;align-items:center;justify-content:center;gap:6px}
.footer{position:absolute;left:0;top:1142px;width:1143px;height:58px;background:var(--footer)}
.copy{position:absolute;left:153px;top:23px;font-family:"Roboto",sans-serif;font-size:11px;color:var(--footer-text)}
.social{position:absolute;right:154px;top:22px;display:flex;gap:14px;font-family:"Roboto",sans-serif;font-size:11px;color:var(--footer-text)}
.social span{display:flex;align-items:center;gap:5px}
.social i{display:block;width:9px;height:9px;background:var(--chip)}
</style>
</head>
<body>
<div class="page">
  <header>
    <div class="brand"><span class="mark"></span>Nora Whitfield Interior Design, LLC</div>
    <div class="rule-top"></div>
    <nav class="nav">
      <a style="left:260px">ENTER</a>
      <a style="left:337px">HOME</a>
      <a style="left:435px">PORTFOLIO</a>
      <a style="left:537px">ABOUT</a>
      <a style="left:653px">PUBLICATIONS</a>
      <a style="left:778px">FINEART</a>
      <a style="left:881px">CONTACT</a>
    </nav>
    <div class="rule-nav"></div>
  </header>

  <div class="hero" role="img" aria-label="Rendered living room with a grey sofa, framed mirror, floor lamp, side tables and vases against a concrete wall"></div>

  <section class="register">
    <div class="title title-top">CLIENT</div>
    <div class="title title-main">REGISTRATION:</div>

    <div class="field" style="left:288px;top:127px"><svg class="ico" viewBox="0 0 10 10"><circle cx="5" cy="3" r="2.3"/><path d="M1 10c0-3 1.8-4.3 4-4.3S9 7 9 10z"/></svg>Name:</div>
    <div class="field" style="left:572px;top:127px"><svg class="ico" viewBox="0 0 10 10"><path d="M2 .5l2 2.3-1 1.2c.6 1.3 1.7 2.4 3 3l1.2-1 2.3 2-1 1.8C4.5 9.6.4 5.5.4 1.5z"/></svg>Work Phone</div>
    <div class="field" style="left:288px;top:171px"><svg class="ico" viewBox="0 0 10 10"><path d="M0 2h10v1L5 6 0 3z"/><path d="M0 4l5 3 5-3v4H0z"/></svg>Email ID:</div>
    <div class="field" style="left:572px;top:171px"><svg class="ico" viewBox="0 0 10 10"><path d="M3 0h4v10H3zM3.8 1v7h2.4V1z"/></svg>Mobile Number:</div>
    <div class="field" style="left:288px;top:215px;width:263px">FN<svg class="chev" viewBox="0 0 8 6"><path d="M1 1l3 3 3-3" stroke="#333" stroke-width="1.3" fill="none"/></svg></div>
    <div class="field" style="left:572px;top:214px">LN<svg class="chev" viewBox="0 0 8 6"><path d="M1 1l3 3 3-3" stroke="#333" stroke-width="1.3" fill="none"/></svg></div>
    <div class="field" style="left:288px;top:258px;width:263px"><svg class="ico" viewBox="0 0 10 10"><path d="M5 0a3.3 3.3 0 0 1 3.3 3.3C8.3 6 5 10 5 10S1.7 6 1.7 3.3A3.3 3.3 0 0 1 5 0zm0 2a1.3 1.3 0 1 0 0 2.6A1.3 1.3 0 0 0 5 2z"/></svg>Property address</div>
    <div class="field" style="left:572px;top:258px;width:264px"><svg class="ico" viewBox="0 0 10 10"><path d="M2 0h6v10H2zM3 1v1.5h1.5V1zm2.5 0v1.5H7V1zM3 3.5V5h1.5V3.5zm2.5 0V5H7V3.5zM3 6v1.5h1.5V6zm2.5 0v1.5H7V6z" fill-rule="evenodd"/></svg>City<svg class="chev" viewBox="0 0 8 6"><path d="M1 1l3 3 3-3" stroke="#333" stroke-width="1.3" fill="none"/></svg></div>
    <div class="field" style="left:288px;top:303px;width:263px">Zip<svg class="chev" viewBox="0 0 8 6"><path d="M1 1l3 3 3-3" stroke="#333" stroke-width="1.3" fill="none"/></svg></div>
    <div class="field" style="left:572px;top:303px;width:264px">Spouse FN<svg class="chev" viewBox="0 0 8 6"><path d="M1 1l3 3 3-3" stroke="#333" stroke-width="1.3" fill="none"/></svg></div>

    <div class="submit"><svg width="12" height="12" viewBox="0 0 12 12"><circle cx="6" cy="6" r="5" fill="none" stroke="#fff" stroke-width="1.6"/><path d="M3.5 6h4M6 4l2 2-2 2" stroke="#fff" stroke-width="1.5" fill="none"/></svg>Submit</div>
  </section>

  <footer class="footer">
    <div class="copy">Copyright © NoraWhitfield 2017. All Right Reserved</div>
    <div class="social">
      <span><i></i>Kinnet</span>
      <span><i></i>Chirply</span>
      <span><i></i>Feedwire</span>
    </div>
  </footer>
</div>
</body>
</html>
```